Business Card Re-Design/Update

We'd like to update out business cards. I've included our current "Style guide" which has the colour scheme of the organisation in it. I've also included the branding files with logos etc in them.

I've also included a copy of one of our existing cards so that you can see how ugly/dated they look. I'd like a fresh modern corporate look.

Target Market(s)

These are for our clients, potential clients, industry contacts - like all business cards

Contact Information for Business Card

Name
Position
Company Address - Level 1, 47 Fernby Street, Carlow Qld 4072
Direct Phone
mobile
Email
Website -www.korvalit.com.au
Logo

Colors

Designer to choose colors to be used in the design.

Requirements
Must have
• Main Logo
• Cards will need to be editable to be able to personalize them for each new employee.
Nice to have
• The MapOut, ShipWell, KeepSteady would be okay to have if they can be sensibly and professionally added to the look without detracting from the main imagery.
• Maybe they could go on the back of the card? will leave this to your creative discretion as to whether/where they fit.
Should not have
• Should not have decorative or script fonts

```html
<!DOCTYPE html>
<html lang="en">
<head>
<meta charset="utf-8">
<title>KorvalIT Business Card</title>
<link href="https://fonts.googleapis.com/css2?family=Open+Sans:wght@400;600;700&display=swap" rel="stylesheet">
<style>
  :root {
    --bg: #e4e6e8;
    --paper: #ffffff;
    --red: #d71920;
    --red-deep: #a8131a;
    --ink: #231f20;
    --grey-text: #5b5b5b;
    --rule: #b8b8b8;
  }
  * { box-sizing: border-box; margin: 0; padding: 0; }
  html, body {
    width: 1200px;
    height: 1200px;
    overflow: hidden;
    background: var(--bg);
    font-family: "Open Sans", Arial, sans-serif;
  }
  .canvas {
    position: relative;
    width: 1200px;
    height: 1200px;
  }
  .card {
    position: absolute;
    left: 158px;
    width: 884px;
    height: 540px;
    overflow: hidden;
    box-shadow: 0 10px 26px rgba(0,0,0,0.14);
  }
  /* ---------- Front ---------- */
  .card-front { top: 40px; background: var(--paper); }
  .brand {
    position: absolute;
    left: 88px;
    top: 232px;
    display: flex;
    align-items: center;
    gap: 18px;
  }
  .brand-square {
    width: 46px;
    height: 46px;
    background: var(--red);
  }
  .brand-name {
    font-weight: 700;
    font-size: 58px;
    letter-spacing: -1px;
    color: var(--ink);
    line-height: 1;
  }
  .divider {
    position: absolute;
    left: 500px;
    top: 58px;
    width: 1px;
    height: 262px;
    background: var(--rule);
  }
  .contact {
    position: absolute;
    left: 528px;
    top: 66px;
    color: var(--grey-text);
    font-size: 15px;
    line-height: 23px;
  }
  .contact-name {
    color: var(--red);
    font-weight: 700;
    font-size: 23px;
    line-height: 30px;
  }
  .contact-role { margin-bottom: 0; }
  .contact-row {
    display: flex;
    align-items: center;
    gap: 9px;
  }
  .contact-row svg { width: 13px; height: 13px; flex: none; }
  .band {
    position: absolute;
    left: 0;
    top: 392px;
    width: 884px;
    height: 62px;
    background: linear-gradient(90deg, var(--red) 0%, var(--red) 62%, #7a1016 76%, #1d1a1b 90%, #111 100%);
  }
  .band-mark {
    position: absolute;
    left: 590px;
    top: 370px;
    width: 44px;
    height: 44px;
    background: var(--paper);
    border: 6px solid var(--red);
    transform: rotate(45deg);
  }
  .strip-white {
    position: absolute;
    left: 0; top: 454px;
    width: 884px; height: 30px;
    background: var(--paper);
  }
  .strip-red {
    position: absolute;
    left: 0; top: 484px;
    width: 884px; height: 56px;
    background: var(--red);
  }
  /* ---------- Back ---------- */
  .card-back { top: 620px; }
  .back-field {
    position: absolute;
    inset: 0;
    background: radial-gradient(ellipse at 30% 20%, #e0222a 0%, var(--red) 45%, var(--red-deep) 100%);
  }
  .services {
    position: absolute;
    left: 0;
    right: 0;
    top: 250px;
    display: flex;
    justify-content: center;
    gap: 26px;
    color: #ffffff;
    font-size: 27px;
    font-weight: 600;
    list-style: none;
  }
  .services li::before {
    content: "•";
    margin-right: 10px;
    font-size: 20px;
    vertical-align: 3px;
  }
</style>
</head>
<body>
<main class="canvas">

  <section class="card card-front" aria-label="Business card front">
    <div class="brand">
      <span class="brand-square"></span>
      <span class="brand-name">korvalIT</span>
    </div>

    <div class="divider"></div>

    <div class="contact">
      <p class="contact-name">Mara Whitfield</p>
      <p class="contact-role">Business Development Manager</p>
      <p>Level 1, 47 Fernby Street</p>
      <p>Carlow Qld 4072</p>
      <p class="contact-row">
        <svg viewBox="0 0 16 16"><path fill="#d71920" d="M3.5 1.5l2.5 0 1 3.5-1.6 1.2a8 8 0 0 0 4.4 4.4L11 9l3.5 1v2.5c0 1-1 2-2 2C6.5 14.5 1.5 9.5 1.5 3.5c0-1 1-2 2-2z"/></svg>
        +61 (07) 3184 6620
      </p>
      <p class="contact-row">
        <svg viewBox="0 0 16 16"><rect x="4" y="1" width="8" height="14" rx="1.5" fill="#d71920"/><rect x="5.5" y="3" width="5" height="8" fill="#fff"/></svg>
        +61 (07) 3184 6620
      </p>
      <p class="contact-row">
        <svg viewBox="0 0 16 16"><rect x="1" y="3" width="14" height="10" rx="1" fill="#d71920"/><path d="M1.5 3.5L8 9l6.5-5.5" fill="none" stroke="#fff" stroke-width="1.4"/></svg>
        info@korvalit.com.au
      </p>
      <p class="contact-row">
        <svg viewBox="0 0 16 16"><circle cx="8" cy="8" r="7" fill="#d71920"/><path d="M1 8h14M8 1c3 3 3 11 0 14M8 1c-3 3-3 11 0 14" fill="none" stroke="#fff" stroke-width="1"/></svg>
        www.korvalit.com.au
      </p>
    </div>

    <div class="band"></div>
    <div class="band-mark"></div>
    <div class="strip-white"></div>
    <div class="strip-red"></div>
  </section>

  <section class="card card-back" aria-label="Business card back">
    <div class="back-field" role="img" aria-label="Red background with a faint repeating brand pattern"></div>
    <ul class="services">
      <li>The MapOut</li>
      <li>ShipWell</li>
      <li>KeepSteady</li>
    </ul>
  </section>

</main>
</body>
</html>
```